Stylish Business Cards Wanted

- DOUBLE SIDED Design Required -

High end, edgy cards for a corporate and personal stylist. Must include logo,
Name: Belinda Harwick
Title: Director and Stylist
telephone : +61 8 7142 5809
email: belinda@theloombriefing.example
website: theloombriefing.example
Tag: Corporate Workwear & Uniform Specialist | Personal Stylist
Would like nice icons for telephone, email, website

Target Market(s)

Businesses wanting stylish uniforms, people wanting stylish wardrobes

Industry/Entity Type

Corporate Workwear Stylist

Contact Information for Business Card

I would like black, white and gold foiling incorporated in the design - possibly a touch of the other colours on my branding guide attached Name: Belinda Harwick Title: Director and Stylist telephone : +61 8 7142 5809 email: belinda@theloombriefing.example website: theloombriefing.example Tag: Corporate Workwear & Uniform Specialist | Personal Stylist Would like nice icons for telephone, email, website

Font styles to use
Other font styles liked:
• Raleway

Colors

Designer to choose colors to be used in the design.

Requirements
Must have
• Gold foil accents

```html
<!DOCTYPE html>
<html lang="en">
<head>
<meta charset="utf-8">
<title>The Loom Briefing – Business Cards</title>
<link rel="stylesheet" href="https://fonts.googleapis.com/css2?family=Arimo:wght@400&family=Montserrat:wght@600&display=swap">
<style>
  :root {
    --ink: #1f1c1d;
    --gold: #e3bb5a;
    --paper: #ffffff;
    --silver: #dfe3e1;
    --stage: #1b1b1b;
  }
  * { margin: 0; padding: 0; box-sizing: border-box; }
  html, body {
    width: 1200px;
    height: 1015px;
    overflow: hidden;
    background: var(--stage);
  }
  .card {
    position: absolute;
    left: 230px;
    width: 740px;
    height: 423px;
    overflow: hidden;
    box-shadow: 0 12px 30px rgba(0,0,0,.55);
  }
  .card--front { top: 60px; background: var(--ink); }
  .card--back  { top: 532px; background: var(--paper); }
  .card__art { position: absolute; inset: 0; width: 740px; height: 423px; }

  .wordmark {
    position: absolute;
    font-family: "Montserrat", sans-serif;
    font-weight: 600;
    text-transform: uppercase;
    line-height: 1.05;
    letter-spacing: .14em;
  }
  .wordmark__small { display: block; font-size: 20px; letter-spacing: .4em; }
  .wordmark__big { display: block; font-size: 58px; letter-spacing: .04em; }
  .wordmark--front { right: 110px; top: 36px; color: var(--silver); text-align: right; }
  .wordmark--back { left: 60px; top: 118px; color: var(--ink); }

  .tagline {
    font-family: "Arimo", sans-serif;
    font-size: 19px;
    fill: var(--ink);
  }

  .contact {
    position: absolute;
    right: 40px;
    bottom: 48px;
    text-align: right;
    font-family: "Arimo", sans-serif;
    color: var(--paper);
  }
  .contact__name {
    font-family: "Montserrat", sans-serif;
    font-weight: 600;
    font-size: 27px;
    color: var(--gold);
    letter-spacing: .02em;
    text-transform: uppercase;
  }
  .contact__title { font-size: 18px; margin-bottom: 14px; }
  .contact__line {
    display: flex;
    justify-content: flex-end;
    align-items: center;
    gap: 8px;
    font-size: 17px;
    line-height: 1.55;
  }
  .contact__icon { width: 16px; height: 16px; fill: var(--gold); }
</style>
</head>
<body>

<section class="card card--front" aria-label="Business card front">
  <svg class="card__art" viewBox="0 0 740 423">
    <path d="M0,423 L0,340 C110,255 240,220 420,200 C560,186 660,170 740,135 L740,423 Z" fill="var(--gold)"/>
    <path id="tagline-curve" d="M80,385 C200,330 360,305 480,288 C580,272 660,250 730,218" fill="none"/>
    <text class="tagline">
      <textPath href="#tagline-curve" startOffset="2%">Corporate Workwear &amp; Uniform Specialist  •  Personal Stylist</textPath>
    </text>
  </svg>
  <div class="wordmark wordmark--front">
    <span class="wordmark__small">The</span>
    <span class="wordmark__big">Loom</span>
    <span class="wordmark__small">Briefing</span>
  </div>
</section>

<section class="card card--back" aria-label="Business card back">
  <svg class="card__art" viewBox="0 0 740 423">
    <path d="M0,423 L0,345 C190,345 300,320 410,215 C510,120 600,60 740,50 L740,423 Z" fill="var(--ink)"/>
    <path d="M0,318 C190,318 290,292 395,190 C480,110 560,70 640,58" fill="none" stroke="var(--gold)" stroke-width="9"/>
    <path d="M0,334 C195,334 300,306 405,205 C500,115 585,62 700,52" fill="none" stroke="var(--ink)" stroke-width="6"/>
  </svg>
  <div class="wordmark wordmark--back">
    <span class="wordmark__small">The</span>
    <span class="wordmark__big">Loom</span>
    <span class="wordmark__small">Briefing</span>
  </div>
  <div class="contact">
    <div class="contact__name">Belinda Harwick</div>
    <div class="contact__title">Director and Stylist</div>
    <div class="contact__line">+61 8 7142 5809
      <svg class="contact__icon" viewBox="0 0 24 24"><path d="M6.6 10.8a15.1 15.1 0 0 0 6.6 6.6l2.2-2.2c.3-.3.7-.4 1-.2 1.1.4 2.3.6 3.6.6.6 0 1 .4 1 1V20c0 .6-.4 1-1 1A17 17 0 0 1 3 4c0-.6.4-1 1-1h3.5c.6 0 1 .4 1 1 0 1.3.2 2.5.6 3.6.1.3 0 .7-.2 1z"/></svg>
    </div>
    <div class="contact__line">theloombriefing.example
      <svg class="contact__icon" viewBox="0 0 24 24"><path d="M12 2a10 10 0 1 0 0 20 10 10 0 0 0 0-20zm6.9 6h-3a15.6 15.6 0 0 0-1.3-3.9A8 8 0 0 1 18.9 8zM12 4c.8 1.2 1.5 2.5 1.9 4h-3.8c.4-1.5 1.1-2.8 1.9-4zM4.3 14a8 8 0 0 1 0-4h3.4a16 16 0 0 0 0 4zm.8 2h3a15.6 15.6 0 0 0 1.3 3.9A8 8 0 0 1 5.1 16zm3-8h-3a8 8 0 0 1 4.3-3.9C8.8 5.3 8.4 6.6 8.1 8zM12 20c-.8-1.2-1.5-2.5-1.9-4h3.8c-.4 1.5-1.1 2.8-1.9 4zm2.3-6H9.7a14.6 14.6 0 0 1 0-4h4.6a14.6 14.6 0 0 1 0 4zm.3 5.9c.6-1.2 1-2.5 1.3-3.9h3a8 8 0 0 1-4.3 3.9zm1.7-5.9a16 16 0 0 0 0-4h3.4a8 8 0 0 1 0 4z"/></svg>
    </div>
    <div class="contact__line">belinda@theloombriefing.example
      <svg class="contact__icon" viewBox="0 0 24 24"><path d="M2 5h20v14H2zm2 2v.4l8 5.2 8-5.2V7zm0 2.8V17h16V9.8l-8 5.2z"/></svg>
    </div>
  </div>
</section>

</body>
</html>
```